Cutting Edge Property Services Provider is Looking to Update Business Card Design

We are looking to freshen up our business cards to match our cutting edge technology based image.

KORVANEX - Where Care Finds Its Pulse

More information about our company can be found on our website at www.korvanex-demo.net

We integrate technology in a historically low tech industry.

We have appeared on the Brisk 300/3000 list 2 years in a row and we're previously recognized as the 5th Quickest Rising Firm in San Diego.

Our core colors are blue and white, but are not against accents that might improve our image.

We currently have our Mission Statement on our Business Cards in a folding design:
KORVANEX IS THE LEADING BUILDING SERVICES INNOVATOR. BY COMBINING TECHNOLOGY WITH FUNCTIONAL TOOS THAT IMPROVE EFFICIENCY IN THE WORKPLACE, WE PROVIDE UNPARALLELED SERVICE IN THE INDUSTRY. DEVELOPING LASTING RELATIONSHIPS WITH OUR CLIENTS AND ASSOCIATES IS THE CORNERSTONE OF OUR SUCCESS.

We'd like to convey the image of a cutting edge, technology based company. Want the cards to pop.

Target Market(s)

Commercial Property Managers - 20 to 50 year old professionals

Industry/Entity Type

Business

Requirements
Must have
• Must utilize our logo obviously, but are definitely open to using variations on the logo. Utilizing the components of the logo, but maybe in different configurations or backgrounds, etc...

Must use the Name: KORVANEX.
Can also use KORVANEX PROPERTY SERVICES.

Must include the Mission Statement

Must say: Where Care Finds Its Pulse
Nice to have
• We are considering plastic stock, shaped cards, or folding cards.

Nothing over the top or really expensive, but will consider if it conveys innovation and technology.
Should not have
• No images of toilets, buildings, trees, or anything relating to commercial properties.

We want to convey our technology image.

```html
<!DOCTYPE html>
<html lang="en">
<head>
<meta charset="utf-8">
<title>Korvanex Folding Business Card</title>
<link rel="stylesheet" href="https://fonts.googleapis.com/css2?family=Open+Sans:wght@400;600;700;800&display=swap">
<style>
  :root {
    --stage-dark: #161616;
    --stage-mid: #2a2a2a;
    --label-red: #e8231f;
    --brand-blue: #164b79;
    --text-blue: #1d5283;
    --strip-grey: #a5a7aa;
    --card-white: #ffffff;
    --card-edge: #d9d9d9;
    --pattern-light: #e3e9ef;
    --pattern-soft: #f3f6f9;
    --ink-dark: #222222;
  }
  * { box-sizing: border-box; margin: 0; padding: 0; }
  html, body { width: 1200px; height: 810px; overflow: hidden; }
  body { font-family: "Open Sans", Arial, sans-serif; }

  .sheet {
    position: relative;
    width: 1200px; height: 810px;
    background: linear-gradient(90deg, var(--stage-dark), var(--stage-mid) 50%, var(--stage-dark));
  }

  .panel-label {
    position: absolute;
    width: 544px;
    text-align: center;
    color: var(--label-red);
    font-weight: 800;
    font-size: 34px;
    letter-spacing: 5px;
  }
  .label-inner-top { left: 52px; top: 20px; }
  .label-front { left: 622px; top: 20px; }
  .label-inner-bottom { left: 52px; top: 726px; }
  .label-back { left: 622px; top: 726px; }

  .card {
    position: absolute;
    width: 544px; height: 309px;
    background: var(--card-white);
    border-radius: 22px;
    border: 1px solid var(--card-edge);
    overflow: hidden;
  }
  .card-inner-top { left: 52px; top: 80px; }
  .card-front { left: 622px; top: 80px; }
  .card-inner-bottom { left: 52px; top: 408px; }
  .card-back { left: 622px; top: 408px; }

  /* Brand name mark */
  .brand-mark {
    position: absolute;
    display: flex; align-items: center; gap: 14px;
    color: var(--brand-blue);
    font-weight: 800;
    letter-spacing: 2px;
  }
  .brand-mark .brand-dot {
    border-radius: 50%;
    background: var(--brand-blue);
    flex: none;
  }

  /* Inner top */
  .card-inner-top .brand-mark { left: 0; right: 0; top: 98px; justify-content: center; font-size: 52px; }
  .card-inner-top .brand-dot { width: 44px; height: 44px; }
  .inner-top-web {
    position: absolute; left: 0; right: 0; top: 266px;
    text-align: center;
    font-size: 19px; letter-spacing: 3px;
    color: var(--ink-dark);
  }

  /* Front */
  .card-front .brand-mark { left: 22px; width: 290px; top: 116px; justify-content: center; font-size: 34px; gap: 10px; }
  .card-front .brand-dot { width: 30px; height: 30px; }
  .web-strip {
    position: absolute; left: 312px; top: 50px;
    width: 20px; height: 220px;
    background: var(--strip-grey);
  }
  .web-strip span {
    position: absolute; left: 50%; top: 50%;
    transform: translate(-50%, -50%) rotate(-90deg);
    white-space: nowrap;
    color: var(--card-white);
    font-size: 12px; letter-spacing: 2px;
  }
  .contact-panel {
    position: absolute; left: 336px; top: 50px;
    width: 220px; height: 220px;
    background: var(--brand-blue);
    color: var(--card-white);
    padding: 22px 0 0 12px;
  }
  .contact-name { font-size: 20px; font-weight: 700; line-height: 1.2; }
  .contact-title { font-size: 13px; margin-bottom: 22px; }
  .contact-line { display: flex; align-items: flex-start; gap: 6px; font-size: 14px; line-height: 18px; }
  .contact-line + .contact-line { margin-top: 4px; }
  .contact-line.address { margin-top: 16px; }
  .contact-line svg { flex: none; width: 11px; height: 11px; margin-top: 4px; }

  /* Inner bottom */
  .faint-backdrop {
    position: absolute; inset: 0;
    background: radial-gradient(ellipse 60% 55% at 40% 50%, var(--pattern-light), var(--card-white) 75%);
  }
  .mission {
    position: absolute; left: 50px; right: 50px; top: 62px;
    text-align: center;
    color: var(--text-blue);
    font-size: 15.5px; line-height: 29.5px;
  }

  /* Back */
  .back-pattern {
    position: absolute; inset: 0;
    background: linear-gradient(180deg, var(--pattern-light), var(--pattern-soft) 50%, var(--pattern-light));
  }
  .card-back .brand-mark { left: 0; right: 0; top: 118px; justify-content: center; font-size: 58px; }
  .card-back .brand-dot { width: 46px; height: 46px; }
  .back-tagline {
    position: absolute; left: 0; right: 0; top: 240px;
    text-align: center;
    color: var(--text-blue);
    font-weight: 700; font-size: 23px;
  }
</style>
</head>
<body>
<main class="sheet">

  <div class="panel-label label-inner-top">Inner Top</div>
  <div class="panel-label label-front">Front</div>
  <div class="panel-label label-inner-bottom">Inner Bottom</div>
  <div class="panel-label label-back">Back</div>

  <section class="card card-inner-top">
    <div class="brand-mark"><span class="brand-dot"></span>KORVANEX</div>
    <p class="inner-top-web">www.korvanex-demo.net</p>
  </section>

  <section class="card card-front">
    <div class="brand-mark"><span class="brand-dot"></span>KORVANEX</div>
    <div class="web-strip"><span>www.korvanex-demo.net</span></div>
    <div class="contact-panel">
      <p class="contact-name">Your Name</p>
      <p class="contact-title">Title</p>
      <p class="contact-line">
        <svg viewBox="0 0 12 12" aria-hidden="true"><path d="M2.5 1 L4.5 1 L5.3 3.5 L4 4.5 Q5 7 7.5 8 L8.5 6.7 L11 7.5 L11 9.5 Q10.5 11 9 11 Q1 10 1 2.5 Q1 1 2.5 1 Z" fill="#fff"/></svg>
        1 (800) 555-0148
      </p>
      <p class="contact-line">
        <svg viewBox="0 0 12 12" aria-hidden="true"><rect x="1" y="3" width="10" height="7" rx="1" fill="#fff"/><path d="M1.5 3.5 L6 7 L10.5 3.5" stroke="#164b79" stroke-width="1" fill="none"/></svg>
        info@korvanex-demo.net
      </p>
      <p class="contact-line address">
        <svg viewBox="0 0 12 12" aria-hidden="true"><circle cx="6" cy="6" r="5.5" fill="#fff"/><circle cx="6" cy="5" r="1.6" fill="#164b79"/><path d="M4.2 6 L6 9 L7.8 6 Z" fill="#164b79"/></svg>
        <span>2150 Harbor Crest Ave.<br>Suite 210<br>San Diego, CA 92108</span>
      </p>
    </div>
  </section>

  <section class="card card-inner-bottom">
    <div class="faint-backdrop" role="img" aria-label="Faint pale blue background decoration"></div>
    <p class="mission">Korvanex is The Leading Building Services Innovator. By Combining Technology With Functional Toos That Improve Efficiency In The Workplace, We Provide Unparalleled Service in The Industry. Developing Lasting Relationships With Our Clients and Associates is The Cornerstone of Our Success.</p>
  </section>

  <section class="card card-back">
    <div class="back-pattern" role="img" aria-label="Pale grey-blue repeating background pattern"></div>
    <div class="brand-mark"><span class="brand-dot"></span>KORVANEX</div>
    <p class="back-tagline">Where Care Finds Its Pulse</p>
  </section>

</main>
</body>
</html>
```